ecommerce news podcast artwork

Podcast cover art for a podcast featuring daily news and events around ecommerce product businesses.

text to be: BRISK LOOP
optional third line of text with smaller font: Podcast

looking for something that pops with a medium to light blue background. text can be in white/red/orange colors. prefer solid colors for text, but background can vary.
I'm really open to other ideas too, sometimes you don't know what you want until you see it.

Target Market(s)

ecommerce business owners, managers

Industry/Entity Type

news, business, ecommerce

Font styles to use
Sans Serif

Colors
0054AA
0677BA
7BADD7
CADEEF
E8F1F8
0094D4
00A9DD
6FCCEA
C7EBF8
E9F6FB
F0912C
F2A743
F7CA91
FBE8D2
FDF5EE
EB3D1F
EC4F4E
F09395
F8D3D4
FCEDEE

Requirements
Must have
• text: BRISK LOOP
Should not have
• no microphones, headsets/headphones, speakers, or other props like that.

```html
<!DOCTYPE html>
<html lang="en">
<head>
<meta charset="UTF-8">
<title>Brisk Loop Podcast Cover</title>
<link rel="stylesheet" href="https://fonts.googleapis.com/css2?family=Archivo+Black&family=Lilita+One&family=Montserrat:wght@400&display=swap">
<style>
  :root {
    --sky-center: #dcfbfd;
    --sky-mid: #c4f1fa;
    --sky-edge: #8cc6df;
    --brand-red: #ff0000;
    --brand-orange: #f3780c;
    --type-white: #ffffff;
    --bag-gold: #f6b53c;
    --cart-peach: #f4b48e;
  }
  html, body {
    margin: 0;
    padding: 0;
    width: 1200px;
    height: 1200px;
    overflow: hidden;
  }
  .cover {
    position: relative;
    width: 1200px;
    height: 1200px;
    background:
      radial-gradient(ellipse at 50% 50%, var(--sky-center) 0%, var(--sky-mid) 62%, var(--sky-edge) 100%);
    overflow: hidden;
  }
  .title-top {
    position: absolute;
    left: 193px;
    top: 238px;
    width: 846px;
    height: 276px;
  }
  .title-top text {
    font-family: "Archivo Black", sans-serif;
    fill: var(--brand-red);
  }
  .title-band {
    position: absolute;
    left: 194px;
    top: 540px;
    width: 844px;
    height: 335px;
    background: var(--brand-orange);
    border-radius: 20px;
  }
  .title-band svg {
    position: absolute;
    left: 44px;
    top: 36px;
    width: 756px;
    height: 266px;
  }
  .title-band text {
    font-family: "Lilita One", sans-serif;
    fill: var(--type-white);
  }
  .show-label {
    position: absolute;
    left: 340px;
    top: 896px;
    width: 520px;
    height: 76px;
  }
  .show-label text {
    font-family: "Montserrat", sans-serif;
    font-weight: 400;
    fill: var(--brand-red);
  }
  .show-label .wave {
    fill: none;
    stroke: var(--brand-red);
    stroke-width: 6;
    stroke-linecap: round;
  }
  .art-cart {
    position: absolute;
    left: 81px;
    top: 666px;
    width: 164px;
    height: 248px;
    border-radius: 18px;
    background: linear-gradient(160deg, var(--bag-gold) 0%, #ee7d78 50%, var(--cart-peach) 100%);
    opacity: 0.85;
  }
  .art-bags {
    position: absolute;
    left: 1123px;
    top: 727px;
    width: 162px;
    height: 187px;
    border-radius: 14px;
    background: linear-gradient(170deg, #fbc95a 0%, var(--bag-gold) 100%);
  }
</style>
</head>
<body>
  <main class="cover">
    <svg class="title-top" viewBox="0 0 846 276" aria-label="BRISK">
      <text x="0" y="266" font-size="330" textLength="846" lengthAdjust="spacingAndGlyphs">BRISK</text>
    </svg>

    <div class="title-band">
      <svg viewBox="0 0 756 266" aria-label="LOOP">
        <text x="0" y="254" font-size="320" textLength="756" lengthAdjust="spacingAndGlyphs">LOOP</text>
      </svg>
    </div>

    <svg class="show-label" viewBox="0 0 520 76" aria-label="Podcast">
      <path class="wave" d="M22 14 Q8 38 22 62"/>
      <path class="wave" d="M38 22 Q29 38 38 54"/>
      <path class="wave" d="M498 14 Q512 38 498 62"/>
      <path class="wave" d="M482 22 Q491 38 482 54"/>
      <text x="260" y="62" font-size="64" text-anchor="middle" textLength="420" lengthAdjust="spacing">PODCAST</text>
    </svg>

    <div class="art-cart" role="img" aria-label="Illustration of a shopping cart holding shopping bags"></div>
    <div class="art-bags" role="img" aria-label="Illustration of two golden shopping bags"></div>
  </main>
</body>
</html>
```